Business card design for Automotive workshop

We need a business card for a new automotive repair and tyre shop called Keelstone Prime Automotive located in New Zealand. We are a clean, modern and fresh workshop and company.

Front needs to feature logo,
my name:
Marlo Fenwicke (director)

Address:
48 Tarn Lane
Marrowby 4172

Phone: 07 594 2713
Mobile: 027 451 9362
Email: office@keelstoneautomotive.example.nz
Website: keelstoneautomotive.example.nz

Back needs to feature an area to write down appointment details, date and time.

Also feature a list of jobs and work we do such as,
Vehicle Servicing
All Mechanical Repairs
Warrant of Fitness
Tyres & Wheel Alignments
Automotive Diagnostics
Automotive Parts & Supplies

```html
<!DOCTYPE html>
<html lang="en">
<head>
<meta charset="utf-8">
<title>Keelstone Prime Automotive – Business Card</title>
<link href="https://fonts.googleapis.com/css2?family=Roboto:wght@400;500;700&family=Open+Sans:wght@400;600&display=swap" rel="stylesheet">
<style>
  :root {
    --red: #e31e24;
    --black: #060606;
    --white: #ffffff;
    --ink: #1a1a1a;
    --rule: #8a8a8a;
    --backdrop: #d9d9d9;
  }
  * { box-sizing: border-box; margin: 0; padding: 0; }
  html, body {
    width: 1200px; height: 802px; overflow: hidden;
    background: var(--backdrop);
    font-family: "Roboto", Arial, sans-serif;
  }
  .stage { position: relative; width: 1200px; height: 802px; }
  .card {
    position: absolute; top: 274px; width: 443px; height: 264px;
    overflow: hidden;
    box-shadow: 2px 3px 6px rgba(0,0,0,0.35);
  }
  .card--front { left: 136px; background: var(--white); }
  .card--back { left: 624px; background: var(--black); }
  .card__shapes { position: absolute; inset: 0; }

  .brand-name {
    position: absolute; left: 0; right: 0;
    text-align: center;
    font-family: "Roboto", Arial, sans-serif;
    font-weight: 700; font-size: 20px; letter-spacing: 1.5px;
    color: var(--red);
  }
  .card--front .brand-name { top: 58px; }
  .card--back .brand-name { top: 53px; }

  .contact-list {
    position: absolute; left: 24px; top: 187px;
    list-style: none; color: var(--white);
    font-size: 12.5px; line-height: 16px;
  }
  .contact-list li { display: flex; align-items: center; gap: 4px; }
  .contact-list svg { width: 10px; height: 10px; fill: var(--red); flex: none; }

  .person {
    position: absolute; right: 24px; top: 180px; text-align: right;
    color: var(--white); font-size: 13px; line-height: 16px;
  }
  .person__name { color: var(--red); font-weight: 700; font-size: 14.5px; letter-spacing: 0.2px; }
  .person__address { margin-top: 10px; }

  .services {
    position: absolute; left: 0; right: 0; top: 106px;
    text-align: center; color: var(--white);
    font-family: "Open Sans", Arial, sans-serif;
    font-size: 12px; line-height: 20px;
  }
  .services .dot {
    display: inline-block; width: 6px; height: 6px; border-radius: 50%;
    background: var(--red); margin: 0 3px 0 5px; vertical-align: 0;
  }
  .appointment {
    position: absolute; left: 0; right: 0; top: 179px; height: 77px;
    background: var(--white); color: var(--ink);
  }
  .appointment__title {
    position: absolute; left: 0; right: 0; top: 15px; text-align: center;
    font-weight: 700; font-size: 15.5px; letter-spacing: 0.2px;
  }
  .appointment__field {
    position: absolute; top: 47px; font-size: 15px; display: flex; align-items: center; gap: 6px;
  }
  .appointment__field .line { display: block; height: 1px; background: var(--rule); }
  .field--date { left: 77px; }
  .field--date .line { width: 90px; }
  .field--time { left: 227px; }
  .field--time .line { width: 90px; }
  .back-strip {
    position: absolute; left: 0; right: 0; bottom: 0; height: 8px; background: var(--red);
  }
</style>
</head>
<body>
<main class="stage">

  <section class="card card--front" aria-label="Business card front">
    <svg class="card__shapes" viewBox="0 0 443 264" aria-hidden="true">
      <rect x="0" y="146" width="443" height="118" fill="var(--black)"/>
      <polygon points="252,146 443,146 443,160 266,160" fill="var(--white)"/>
      <polygon points="262,146 443,146 443,157 273,157" fill="var(--red)"/>
    </svg>
    <div class="brand-name">KEELSTONE PRIME AUTOMOTIVE</div>

    <ul class="contact-list">
      <li><svg viewBox="0 0 10 10"><path d="M1 3c0-2 8-2 8 0v1H7V3H3v1H1zM2 5h6l1 4H1z"/></svg>07 594 2713</li>
      <li><svg viewBox="0 0 10 10"><path d="M2.5 0h5v10h-5zM3.5 1.2v6.6h3V1.2z"/></svg>027 451 9362</li>
      <li><svg viewBox="0 0 10 10"><path d="M0 2h10v6H0zM0.8 2.6 5 5.6l4.2-3z" fill-rule="evenodd"/></svg>office@keelstoneautomotive.example.nz</li>
      <li><svg viewBox="0 0 10 10"><circle cx="5" cy="5" r="4.5"/></svg>keelstoneautomotive.example.nz</li>
    </ul>

    <div class="person">
      <div class="person__name">MARLO FENWICKE</div>
      <div class="person__role">Director</div>
      <div class="person__address">48 Tarn Lane<br>Marrowby 4172</div>
    </div>
  </section>

  <section class="card card--back" aria-label="Business card back">
    <div class="brand-name">KEELSTONE PRIME AUTOMOTIVE</div>
    <p class="services">
      Vehicle Servicing<span class="dot"></span>All Mechanical Repairs<span class="dot"></span>Warrant of Fitness<br>
      Tyres &amp; Wheel Alignments<span class="dot"></span>Automotive Diagnostics<br>
      Automotive Parts &amp; Supplies
    </p>
    <div class="appointment">
      <div class="appointment__title">NEXT APPOINTMENT</div>
      <div class="appointment__field field--date">DATE <span class="line"></span></div>
      <div class="appointment__field field--time">TIME <span class="line"></span></div>
    </div>
    <div class="back-strip"></div>
  </section>

</main>
</body>
</html>
```